Oakmere Animal Care Group of Central Pennsylvania

I need a business card design for a new company in Harrisburg PA called "Animal Care Oakmere Group of Central PA". I will be providing relief services for veterinarians who need coverage during vacations; sick/maternity leave, etc. I would like to see the veterinarian symbol incorporated in the design in combination with animals (dogs /cats/birds/reptiles an pocket pets). Include My full name: Tomás R. Quintaval DVM, MLAS, BS. Also include my e mail (dvmtrq@mailbrook.net) and phone number 5552846017

Target Market(s)

Small Animal Veterinarian, practice owner

Industry/Entity Type

Business

Contact Information for Business Card

Oakmere Animal Care Group of Central PA

Font styles to use
Script

Requirements
Must have
• Veterinarian caduceus (see image) and Small animals (pets) within the logo.
Nice to have
• Give a sense of relaxation (vacationing)
Should not have
• Large animals, i.e. horses, cows, zoo animals...

```html
<!DOCTYPE html>
<html lang="en">
<head>
<meta charset="utf-8">
<title>Animal Care Oakmere Group of Central PA — Business Card</title>
<link rel="stylesheet" href="https://fonts.googleapis.com/css2?family=Cinzel:wght@600&family=Italianno&family=Lora:wght@500&display=swap">
<style>
  :root {
    --page-bg: #e9e7e3;
    --card-bg: #ffffff;
    --card-shade: #f1f0ee;
    --brand-red: #a5182a;
    --brand-red-light: #c43a4b;
    --ink: #1b1b1b;
    --rule: #3a3a3a;
    --paw-tone: #d9d9d9;
  }
  html, body {
    margin: 0;
    width: 1200px;
    height: 892px;
    overflow: hidden;
    background: var(--page-bg);
  }
  .business-card {
    position: absolute;
    left: 150px;
    top: 189px;
    width: 900px;
    height: 514px;
    background: linear-gradient(135deg, var(--card-bg) 40%, var(--card-shade));
    box-shadow: 0 6px 24px rgba(0,0,0,0.18);
    overflow: hidden;
  }
  .corner-accents {
    position: absolute;
    inset: 0;
  }
  .brand-block {
    position: absolute;
    left: 110px;
    top: 40px;
    width: 360px;
    text-align: center;
  }
  .brand-mark {
    width: 96px;
    height: 96px;
    margin: 0 auto 14px;
    border-radius: 50%;
    border: 6px solid var(--brand-red);
    box-sizing: border-box;
  }
  .brand-name {
    margin: 0;
    font-family: "Cinzel", serif;
    font-weight: 600;
    font-size: 21px;
    line-height: 1.2;
    letter-spacing: 0.5px;
    color: var(--brand-red);
  }
  .holder {
    position: absolute;
    right: 390px;
    top: 246px;
    width: 400px;
    margin: 0;
    text-align: right;
    font-family: "Italianno", cursive;
    font-weight: 400;
    color: var(--ink);
  }
  .holder-name {
    display: block;
    font-size: 62px;
    line-height: 1;
  }
  .holder-credentials {
    display: block;
    font-size: 36px;
    line-height: 1.1;
  }
  .divider {
    position: absolute;
    left: 535px;
    top: 245px;
    width: 1px;
    height: 130px;
    background: var(--rule);
  }
  .contact-list {
    position: absolute;
    left: 565px;
    top: 270px;
    margin: 0;
    padding: 0;
    list-style: none;
    font-family: "Lora", serif;
    font-weight: 500;
    font-size: 21px;
    color: var(--ink);
    letter-spacing: 0.5px;
  }
  .contact-item {
    display: flex;
    align-items: center;
    gap: 16px;
    height: 40px;
  }
  .contact-icon {
    width: 18px;
    height: 18px;
    fill: var(--ink);
  }
  .paw-trail {
    position: absolute;
    left: 560px;
    top: 170px;
    width: 110px;
    height: 40px;
    border-radius: 6px;
    background: linear-gradient(90deg, var(--paw-tone), rgba(217,217,217,0.3));
  }
</style>
</head>
<body>
  <main class="business-card">
    <svg class="corner-accents" width="900" height="514" viewBox="0 0 900 514" aria-hidden="true">
      <defs>
        <linearGradient id="accentRed" x1="0" y1="0" x2="1" y2="1">
          <stop offset="0" stop-color="#c43a4b"/>
          <stop offset="1" stop-color="#a5182a"/>
        </linearGradient>
      </defs>
      <polygon points="0,290 0,514 230,514" fill="url(#accentRed)"/>
      <polygon points="900,0 690,0 900,200" fill="url(#accentRed)"/>
    </svg>

    <header class="brand-block">
      <div class="brand-mark" aria-hidden="true"></div>
      <p class="brand-name">Animal Care Oakmere Group<br>of Central PA</p>
    </header>

    <div class="paw-trail" role="img" aria-label="Trail of small paw prints"></div>

    <h1 class="holder">
      <span class="holder-name">Tomás R. Quintaval</span>
      <span class="holder-credentials">DVM, MLAS, BS</span>
    </h1>
    <div class="divider"></div>

    <ul class="contact-list">
      <li class="contact-item">
        <svg class="contact-icon" viewBox="0 0 24 24" aria-hidden="true">
          <path d="M6.6 10.8c1.4 2.8 3.8 5.1 6.6 6.6l2.2-2.2c.3-.3.7-.4 1-.2 1.1.4 2.300.6 3.6.6.6 0 1 .4 1 1V20c0 .6-.4 1-1 1C10.6 21 3 13.4 3 4c0-.6.4-1 1-1h3.5c.6 0 1 .4 1 1 0 1.3.2 2.5.6 3.6.1.3 0 .7-.2 1L6.6 10.8z"/>
        </svg>
        <span>5552846017</span>
      </li>
      <li class="contact-item">
        <svg class="contact-icon" viewBox="0 0 24 24" aria-hidden="true">
          <path d="M2 5h20v14H2z M3.5 6.5 12 13l8.5-6.5" fill="#1b1b1b" stroke="#fff" stroke-width="1.3"/>
        </svg>
        <span>dvmtrq@mailbrook.net</span>
      </li>
    </ul>
  </main>
</body>
</html>
```